Fitness website

Website for a fitness brand (see attached specs). Design needs to be modern and vibrant with CTAs on every page. We will provide logos, images, etc but for now user placeholder text and images. For now use the name 'Corvane Athletics' as the name to use on the design. The goal of this site is to either get people to join the gym (5 physical locations across the US); buy an online program; buy merch or supplements or sign up for the newsletter. Pleas use images from this foldeR: https://filebarn.example/share/folders/8QwTz41mKpLrXv93NdYe7HsaBuJ0Cf2_R?usp=sharing

We will be coding this in ReactNative. Lots more work for the winner as well, this is a 1st project for us.

Target Market(s)

fitness enthusiats

Industry/Entity Type

fitness, health, wellness

Number of Pages Required

5+ page

Font styles to use
Other font styles liked:
• Lato

Colors
0054AA
0677BA
7BADD7
CADEEF
E8F1F8
0094D4
00A9DD
6FCCEA
C7EBF8
E9F6FB
00AB8E
00BBA5
67D7C9
C6EFE9
E9F9F6
EE7325
F08F49
F5BC92
FAE3D3
FDF4ED

Requirements
Must have
• must be reactive. most people will view it first on mobile
Nice to have
• video in hero section of top of home page

```html
<!DOCTYPE html>
<html lang="en">
<head>
<meta charset="utf-8">
<title>Corvane Athletics — Home</title>
<link href="https://fonts.googleapis.com/css2?family=Lato:wght@300;400;700;900&display=swap" rel="stylesheet">
<style>
:root{
  --blue:#0054AA;
  --blue-mid:#0677BA;
  --blue-bright:#1a7fd0;
  --navy:#16389a;
  --navy-deep:#12308a;
  --orange:#EE7325;
  --orange-deep:#e0571c;
  --pale:#E8F1F8;
  --pale-2:#dde8f4;
  --ink:#333;
  --muted:#555;
  --white:#fff;
  --ghost:#eeeeee;
}
*{box-sizing:border-box;margin:0;padding:0}
html,body{width:1200px;height:4835px;overflow:hidden;background:#fff;font-family:'Lato',sans-serif;color:var(--ink)}
.page{position:relative;width:1200px;height:4835px;overflow:hidden}
.abs{position:absolute}
svg.abs{display:block}
.btn{position:absolute;display:flex;align-items:center;justify-content:center;gap:10px;border-radius:28px;color:#fff;font-weight:700;font-size:15px;text-transform:uppercase;letter-spacing:.2px}
.btn .dot{width:18px;height:18px;border-radius:50%;background:#fff;display:flex;align-items:center;justify-content:center}
.btn-blue{background:var(--blue-bright)}
.btn-orange{background:var(--orange-deep)}
.ghost{position:absolute;font-weight:900;text-transform:uppercase;line-height:1;white-space:nowrap}
.h2{position:absolute;font-weight:900;text-transform:uppercase;font-size:45px;letter-spacing:-.5px;white-space:nowrap}
.h2 .accent{color:var(--blue-bright)}
.photo{position:absolute}
/* header */
.logo{position:absolute;color:#fff;font-weight:700;line-height:1}
.logo .l1{font-size:46px;letter-spacing:.5px}
.logo .l2{font-size:25px;letter-spacing:6px;margin-top:10px}
.nav{position:absolute;display:flex;gap:30px;font-size:15px;font-weight:700;text-transform:uppercase;color:#fff}
.nav .active{position:relative}
.nav .active::after{content:"";position:absolute;left:0;right:0;bottom:-14px;height:3px;background:var(--blue-bright)}
/* about */
.body-text{position:absolute;font-size:15px;line-height:27.6px;color:var(--muted);text-align:justify}
/* program cards */
.card{position:absolute;background:#fff;text-align:center}
.card .img{height:241px}
.card h3{font-size:22px;font-weight:700;color:#222;margin-top:30px}
.card p{font-size:17px;line-height:25px;color:var(--muted);margin:12px 26px 0}
.card .bar{position:absolute;left:0;right:0;bottom:0;height:7px;background:#d9e6f3}
.card .bar.on{background:var(--blue-bright)}
.card .knob{position:absolute;left:50%;bottom:-15px;margin-left:-19px;width:38px;height:38px;border-radius:50%;background:#fff;border:3px solid #d9e6f3;display:flex;align-items:center;justify-content:center}
.card .knob.on{background:var(--blue-bright);border-color:#fff}
.arrow-round{position:absolute;width:40px;height:40px;border-radius:50%;border:2px solid #bbb;display:flex;align-items:center;justify-content:center}
/* locations */
.city{position:absolute;text-align:center;font-size:21px;font-weight:700;color:#222}
/* reviews */
.review{position:absolute;background:#fff;text-align:center;box-shadow:0 4px 14px rgba(0,40,100,.12)}
.review .q{font-size:64px;font-weight:900;color:var(--blue-bright);line-height:1;height:42px;margin-top:24px;font-family:Georgia,serif}
.review p{font-size:14.5px;line-height:24px;color:var(--muted);margin:6px 26px 0}
.review hr{border:0;border-top:1px solid #ddd;margin:22px 16px 0}
.review .author{display:flex;align-items:center;justify-content:center;gap:14px;margin-top:18px;text-align:left}
.review .avatar{width:40px;height:40px;border-radius:50%;background:#c9b7a6;flex:none}
.review .name{font-size:16px;font-weight:700;color:#222;line-height:19px}
.review .loc{font-size:11px;color:#555;margin-top:3px;line-height:13px}
.review .tail{position:absolute;left:50%;bottom:-13px;margin-left:-13px;width:0;height:0;border-left:13px solid transparent;border-right:13px solid transparent;border-top:14px solid #fff}
.review.on .tail{border-top-color:var(--blue-bright)}
.review.on .bar{position:absolute;left:0;right:0;bottom:-7px;height:7px;background:var(--blue-bright)}
/* footer */
.fnav{position:absolute;display:flex;gap:32px;color:#fff;font-weight:700;font-size:16px;text-transform:uppercase}
.contact{position:absolute;display:flex;align-items:center;gap:26px;color:#fff}
.contact .ic{width:80px;height:80px;border-radius:50%;background:rgba(255,255,255,.12);display:flex;align-items:center;justify-content:center}
.contact .ic.hot{background:var(--orange-deep)}
.contact .lbl{font-size:15px}
.contact .val{font-size:13.5px;line-height:24px;margin-top:4px}
.social{position:absolute;width:42px;height:42px;border-radius:50%;border:2px solid rgba(255,255,255,.35);display:flex;align-items:center;justify-content:center}
.social.on{background:var(--blue-bright);border-color:var(--blue-bright)}
.social i{width:10px;height:10px;border-radius:50%;background:#fff;display:block}
</style>
</head>
<body>
<div class="page">

<!-- ===== HERO ===== -->
<div class="photo" role="img" aria-label="Athlete lifting a barbell in a dim gym, hero video still" style="left:0;top:0;width:1200px;height:880px;background:radial-gradient(ellipse at 62% 30%,#6a4f43 0%,#3a2e2b 30%,#1d1d22 65%,#121318 100%)"></div>
<div class="abs" style="left:0;top:136px;width:1200px;height:1px;background:rgba(255,255,255,.25)"></div>
<svg class="abs" style="left:0;top:690px" width="1200" height="200" viewBox="0 0 1200 200">
  <polygon points="0,108 1200,178 1200,200 0,200" fill="#fff"/>
  <polygon points="0,0 302,62 0,108" fill="var(--blue)"/>
</svg>

<div class="logo" style="left:142px;top:26px"><div class="l1">CORVANE</div><div class="l2">ATHLETICS</div></div>

<div class="abs" style="left:628px;top:24px;width:30px;height:30px;border-radius:50%;background:var(--blue);display:flex;align-items:center;justify-content:center">
  <svg width="14" height="14" viewBox="0 0 24 24"><path d="M6.6 10.8a15.1 15.1 0 0 0 6.6 6.6l2.2-2.2c.3-.3.7-.4 1-.2 1.1.4 2.3.6 3.6.6.6 0 1 .4 1 1V20c0 .6-.4 1-1 1C10.6 21 3 13.4 3 4c0-.6.4-1 1-1h3.5c.6 0 1 .4 1 1 0 1.3.2 2.5.6 3.6.1.3 0 .7-.2 1z" fill="#fff"/></svg>
</div>
<div class="abs" style="left:676px;top:24px;color:#fff;font-size:13px;font-weight:700">CALL US</div>
<div class="abs" style="left:676px;top:46px;color:#fff;font-size:17px;font-weight:700">+1 555 014 2287</div>
<div class="btn btn-orange" style="left:841px;top:19px;width:214px;height:52px;font-size:15px">Buy Online Program</div>

<nav class="nav" style="left:524px;top:101px">
  <span class="active">Home</span><span>About</span><span>Programs</span><span>Shop</span><span>Blog</span><span>Contact</span>
  <svg width="16" height="16" viewBox="0 0 24 24" style="margin-left:-6px"><circle cx="10" cy="10" r="7" fill="none" stroke="#fff" stroke-width="3"/><line x1="15" y1="15" x2="22" y2="22" stroke="#fff" stroke-width="3"/></svg>
</nav>

<h1 class="abs" style="left:0;width:1200px;top:414px;text-align:center;color:#fff;font-weight:900;font-size:66px;letter-spacing:-1px;text-transform:uppercase">Transform Your Body</h1>
<div class="btn btn-blue" style="left:340px;top:535px;width:254px;height:53px">View Our Programs <span class="dot"><svg width="10" height="10" viewBox="0 0 10 10"><path d="M3 1.5 6.5 5 3 8.5" stroke="var(--blue-bright)" stroke-width="2" fill="none"/></svg></span></div>
<div class="btn btn-orange" style="left:607px;top:535px;width:254px;height:53px">Join The Gym <span class="dot"><svg width="10" height="10" viewBox="0 0 10 10"><path d="M3 1.5 6.5 5 3 8.5" stroke="var(--orange-deep)" stroke-width="2" fill="none"/></svg></span></div>
<svg class="abs" style="left:570px;top:651px" width="58" height="58" viewBox="0 0 58 58"><circle cx="29" cy="29" r="26" fill="none" stroke="#fff" stroke-width="4"/><polygon points="23,18 40,29 23,40" fill="#fff"/></svg>

<!-- ===== ABOUT ===== -->
<h2 class="h2" style="left:145px;top:950px;color:var(--blue)">About <span class="accent">Us</span></h2>
<p class="body-text" style="left:145px;top:1026px;width:401px">Sed ut perspiciatis unde omnis iste natus error sit voluptatem accusantium doloremque laudantium, totam rem aperiam, eaque ipsa quae ab illo inventore veritatis et quasi architecto beatae vitae dicta sunt explicabo. Nemo enim ipsam voluptatem quia voluptas sit aspernatur aut odit aut fugit, sed quia consequuntur magni dolores eos qui ratione voluptatem sequi neque porro quisquam est, qui dolorem ipsum quia dolor sit amet.</p>
<p class="body-text" style="left:145px;top:1275px;width:401px">Nemo enim ipsam voluptatem quia voluptas sit aspernatur aut odit aut fugit, sed quia consequuntur magni dolores eos qui ratione voluptatem sequi neque porro quisquam est, qui dolorem ipsum quia dolor.</p>
<div class="btn btn-blue" style="left:145px;top:1424px;width:180px;height:53px">Read More <span class="dot"><svg width="10" height="10" viewBox="0 0 10 10"><path d="M3 1.5 6.5 5 3 8.5" stroke="var(--blue-bright)" stroke-width="2" fill="none"/></svg></span></div>
<div class="ghost" style="left:360px;top:1420px;font-size:88px;color:var(--ghost)">About</div>

<svg class="abs" style="left:714px;top:1196px" width="345" height="362" viewBox="0 0 345 362">
  <polyline points="304,2 342,2 342,359 3,359 3,90" fill="none" stroke="var(--orange-deep)" stroke-width="4"/>
</svg>
<div class="photo" role="img" aria-label="Athlete pressing a loaded barbell overhead at a competition" style="left:599px;top:883px;width:400px;height:503px;background:linear-gradient(160deg,#2b3a55 0%,#4a4f5c 45%,#2a2a31 100%)"></div>
<div class="photo" role="img" aria-label="Blue-toned video still of athletes training, with play button" style="left:768px;top:1296px;width:316px;height:206px;background:linear-gradient(135deg,#1e6fc0,#0d4e9a)"></div>
<svg class="abs" style="left:900px;top:1373px" width="52" height="52" viewBox="0 0 52 52"><circle cx="26" cy="26" r="24" fill="rgba(255,255,255,.85)"/><polygon points="21,16 36,26 21,36" fill="var(--blue-bright)"/></svg>

<!-- ===== PROGRAMS ===== -->
<svg class="abs" style="left:0;top:1555px" width="1200" height="640" viewBox="0 0 1200 640">
  <defs><linearGradient id="progBg" x1="0" y1="0" x2="1" y2="0"><stop offset="0" stop-color="#143f9f"/><stop offset="1" stop-color="#1c6cbf"/></linearGradient></defs>
  <polygon points="0,4 1200,90 1200,455 0,625" fill="url(#progBg)"/>
  <polygon points="700,54 1200,90 1200,200" fill="#2a7fd0" opacity=".6"/>
</svg>
<div class="ghost" style="left:22px;top:1643px;font-size:88px;color:rgba(255,255,255,.07)">Programs</div>
<h2 class="h2" style="left:0;width:1200px;text-align:center;top:1747px;color:#fff">Online Programs</h2>
<div class="abs" style="left:0;width:1200px;text-align:center;top:1822px;color:#fff;font-size:26px;font-weight:700">Train Anywhere, Anytime</div>

<div class="arrow-round" style="left:57px;top:2095px;border-color:#9fb7dd"><svg width="12" height="14" viewBox="0 0 12 14"><path d="M8 1 2 7l6 6" stroke="#9fb7dd" stroke-width="2" fill="none"/></svg></div>
<div class="arrow-round" style="left:1101px;top:2095px"><svg width="12" height="14" viewBox="0 0 12 14"><path d="M4 1l6 6-6 6" stroke="#aaa" stroke-width="2" fill="none"/></svg></div>

<div class="card" style="left:143px;top:1915px;width:285px;height:408px">
  <div class="img" role="img" aria-label="Athlete walking between rigs in a dark arena" style="background:linear-gradient(180deg,#3a3a3f,#1e1e22)"></div>
  <h3>Corvane Performance</h3>
  <p>Sed ut perspiciatis unde omnis iste natus error sit voluptatem accusantium doloremqu</p>
  <div class="bar on"></div>
  <div class="knob on"><svg width="14" height="14" viewBox="0 0 14 14"><circle cx="7" cy="7" r="6" fill="none" stroke="#fff" stroke-width="1.5"/><path d="M6 4l3 3-3 3" stroke="#fff" stroke-width="1.5" fill="none"/></svg></div>
</div>
<div class="card" style="left:456px;top:1915px;width:286px;height:408px">
  <div class="img" role="img" aria-label="Two athletes kneeling and training on the gym floor" style="background:linear-gradient(180deg,#4b4a47,#25282a)"></div>
  <h3>Corvane Masters</h3>
  <p>Sed ut perspiciatis unde omnis iste natus error sit voluptatem accusantium doloremqu</p>
  <div class="bar"></div>
  <div class="knob"><svg width="14" height="14" viewBox="0 0 14 14"><circle cx="7" cy="7" r="6" fill="none" stroke="var(--blue-bright)" stroke-width="1.5"/><path d="M6 4l3 3-3 3" stroke="var(--blue-bright)" stroke-width="1.5" fill="none"/></svg></div>
</div>
<div class="card" style="left:772px;top:1915px;width:285px;height:408px">
  <div class="img" role="img" aria-label="Athlete gripping a loaded barbell before a lift" style="background:linear-gradient(180deg,#3b4656,#22262d)"></div>
  <h3>Corvane Weightlifting</h3>
  <p>Sed ut perspiciatis unde omnis iste natus error sit voluptatem accusantium doloremqu</p>
  <div class="bar"></div>
  <div class="knob"><svg width="14" height="14" viewBox="0 0 14 14"><circle cx="7" cy="7" r="6" fill="none" stroke="var(--blue-bright)" stroke-width="1.5"/><path d="M6 4l3 3-3 3" stroke="var(--blue-bright)" stroke-width="1.5" fill="none"/></svg></div>
</div>

<div class="btn btn-blue" style="left:308px;top:2404px;width:286px;height:52px">View All Programs <span class="dot"><svg width="10" height="10" viewBox="0 0 10 10"><path d="M3 1.5 6.5 5 3 8.5" stroke="var(--blue-bright)" stroke-width="2" fill="none"/></svg></span></div>
<div class="btn btn-orange" style="left:607px;top:2404px;width:286px;height:52px">Start My Online Journey <span class="dot"><svg width="10" height="10" viewBox="0 0 10 10"><path d="M3 1.5 6.5 5 3 8.5" stroke="var(--orange-deep)" stroke-width="2" fill="none"/></svg></span></div>

<!-- ===== LOCATIONS ===== -->
<div class="ghost" style="left:0;width:1200px;text-align:center;top:2560px;font-size:90px;color:var(--ghost)">Our Locations</div>
<h2 class="h2" style="left:0;width:1200px;text-align:center;top:2590px;color:var(--navy)">Our <span class="accent">Locations</span></h2>

<div class="photo" role="img" aria-label="San Diego skyline at dusk" style="left:9px;top:2695px;width:228px;height:246px;clip-path:polygon(0 6%,100% 0,100% 100%,0 100%);background:linear-gradient(180deg,#3b3c8a,#6a3f7a 55%,#101430)"></div>
<div class="photo" role="img" aria-label="Boston skyline and bridge reflected at night" style="left:248px;top:2695px;width:228px;height:246px;clip-path:polygon(0 0,100% 3%,100% 100%,0 100%);background:linear-gradient(180deg,#1e4aa8,#0f2a66 55%,#1a3d8a)"></div>
<div class="photo" role="img" aria-label="Miami skyline across the bay on a bright day" style="left:486px;top:2695px;width:228px;height:246px;background:linear-gradient(180deg,#8dc4ec,#c9dfe9 40%,#4a88a8 70%,#2e6e8e)"></div>
<div class="photo" role="img" aria-label="Seattle skyline with its tower at sunset" style="left:725px;top:2695px;width:227px;height:246px;clip-path:polygon(0 0,100% 3%,100% 100%,0 100%);background:linear-gradient(180deg,#5f7b9c,#d39a62 55%,#3a3440)"></div>
<div class="photo" role="img" aria-label="Capitol building reflected in water at dusk" style="left:962px;top:2695px;width:228px;height:246px;clip-path:polygon(0 4%,100% 0,100% 100%,0 100%);background:linear-gradient(180deg,#6b86b8,#2c3f6a 60%,#1c2438)"></div>

<div class="city" style="left:9px;width:228px;top:2965px">San Diego</div>
<div class="city" style="left:248px;width:228px;top:2965px">Boston</div>
<div class="city" style="left:486px;width:228px;top:2965px">Miami</div>
<div class="city" style="left:725px;width:227px;top:2965px">Seattle</div>
<div class="city" style="left:962px;width:228px;top:2965px">DC</div>

<!-- ===== REVIEWS ===== -->
<svg class="abs" style="left:0;top:3065px" width="1200" height="950" viewBox="0 0 1200 950">
  <polygon points="0,158 1200,4 1200,935 0,750" fill="var(--pale)"/>
  <polygon points="0,750 1200,935 1200,950 0,950" fill="#fff"/>
</svg>
<h2 class="h2" style="left:0;width:1200px;text-align:center;top:3283px;color:var(--navy)">What Our <span class="accent">Customers Say</span></h2>

<div class="arrow-round" style="left:57px;top:3497px"><svg width="12" height="14" viewBox="0 0 12 14"><path d="M8 1 2 7l6 6" stroke="#aaa" stroke-width="2" fill="none"/></svg></div>
<div class="arrow-round" style="left:1101px;top:3497px"><svg width="12" height="14" viewBox="0 0 12 14"><path d="M4 1l6 6-6 6" stroke="#aaa" stroke-width="2" fill="none"/></svg></div>

<div class="review" style="left:135px;top:3386px;width:301px;height:286px">
  <div class="q">“</div>
  <p>“In ullamcorper est eget tempor cursus neque mi consectetuer mi a ultricies massa est sed nisl Class aptent taciti so litora torquent”</p>
  <hr>
  <div class="author"><div class="avatar" role="img" aria-label="Reviewer portrait"></div><div><div class="name">By Author Name</div><div class="loc">City, Location</div></div></div>
  <div class="tail"></div>
</div>
<div class="review on" style="left:449px;top:3386px;width:304px;height:286px">
  <div class="q">“</div>
  <p>“In ullamcorper est eget tempor cursus neque mi consectetuer mi a ultricies massa est sed nisl Class aptent taciti so litora torquent”</p>
  <hr>
  <div class="author"><div class="avatar" role="img" aria-label="Reviewer portrait" style="background:#7d7f86"></div><div><div class="name">By Author Name</div><div class="loc">City, Location</div></div></div>
  <div class="bar"></div>
  <div class="tail" style="bottom:-20px"></div>
</div>
<div class="review" style="left:772px;top:3386px;width:293px;height:286px">
  <div class="q">“</div>
  <p>“ In ullamcorper est eget tempor cursus neque mi consectetuer mi a ultricies massa est sed nisl Class aptent taciti so litora torquent”</p>
  <hr>
  <div class="author"><div class="avatar" role="img" aria-label="Reviewer portrait" style="background:#8a6f5e"></div><div><div class="name">By Author Name</div><div class="loc">City, Location</div></div></div>
  <div class="tail"></div>
</div>

<div class="ghost" style="left:751px;top:3725px;font-size:86px;color:rgba(255,255,255,.75)">Reviews</div>
<div class="btn btn-orange" style="left:473px;top:3733px;width:254px;height:53px">View More Reviews <span class="dot"><svg width="10" height="10" viewBox="0 0 10 10"><path d="M3 1.5 6.5 5 3 8.5" stroke="var(--orange-deep)" stroke-width="2" fill="none"/></svg></span></div>

<!-- ===== NEWSLETTER ===== -->
<div class="ghost" style="left:52px;top:4222px;font-size:76px;color:#e9eef6;transform:rotate(-90deg);transform-origin:0 0">Join Us</div>
<h2 class="h2" style="left:0;width:1200px;text-align:center;top:4032px;font-size:41px;color:var(--navy)">Stay Strong. <span class="accent">Stay Informed.</span></h2>
<div class="abs" style="left:0;width:1200px;text-align:center;top:4110px;font-size:21px;color:#444">Join our newsletter for free training tips, events, and exclusive offers.</div>
<div class="abs" style="left:327px;top:4184px;width:381px;height:53px;border:1px solid #bbb;border-radius:28px;padding-left:34px;display:flex;align-items:center;font-size:15px;color:#444">Enter Email</div>
<div class="btn btn-orange" style="left:716px;top:4184px;width:159px;height:53px">Join Now <span class="dot"><svg width="10" height="10" viewBox="0 0 10 10"><path d="M3 1.5 6.5 5 3 8.5" stroke="var(--orange-deep)" stroke-width="2" fill="none"/></svg></span></div>

<!-- ===== FOOTER ===== -->
<svg class="abs" style="left:0;top:4245px" width="1200" height="590" viewBox="0 0 1200 590">
  <polygon points="0,0 1200,64 1200,590 0,590" fill="var(--navy)"/>
  <polygon points="900,85 1200,40 1200,152" fill="var(--blue-bright)"/>
</svg>
<div class="logo" style="left:142px;top:4440px"><div class="l1">CORVANE</div><div class="l2">ATHLETICS</div></div>
<nav class="fnav" style="left:517px;top:4467px"><span>Home</span><span>About</span><span>Programs</span><span>Shop</span><span>Blog</span><span>Contact</span></nav>
<div class="abs" style="left:142px;top:4560px;width:915px;height:1px;background:rgba(255,255,255,.2)"></div>

<div class="contact" style="left:167px;top:4602px">
  <div class="ic"><svg width="34" height="30" viewBox="0 0 34 30"><path d="M17 2 2 15h4v13h8v-9h6v9h8V15h4z" fill="#fff"/></svg></div>
  <div><div class="lbl">Address</div><div class="val">123, Sed ut perspiciande<br>omnis istoluptatem</div></div>
</div>
<div class="abs" style="left:447px;top:4588px;width:1px;height:105px;background:rgba(255,255,255,.2)"></div>
<div class="contact" style="left:488px;top:4602px">
  <div class="ic hot"><svg width="34" height="24" viewBox="0 0 34 24"><rect x="1" y="1" width="32" height="22" rx="3" fill="#fff"/><path d="M2 3l15 11L32 3" stroke="var(--orange-deep)" stroke-width="2.5" fill="none"/></svg></div>
  <div><div class="lbl">Email Us</div><div class="val">hello@corvanemail.example</div></div>
</div>
<div class="abs" style="left:783px;top:4588px;width:1px;height:105px;background:rgba(255,255,255,.2)"></div>
<div class="contact" style="left:826px;top:4602px">
  <div class="ic"><svg width="32" height="32" viewBox="0 0 24 24"><path d="M6.6 10.8a15.1 15.1 0 0 0 6.6 6.6l2.2-2.2c.3-.3.7-.4 1-.2 1.1.4 2.3.6 3.6.6.6 0 1 .4 1 1V20c0 .6-.4 1-1 1C10.6 21 3 13.4 3 4c0-.6.4-1 1-1h3.5c.6 0 1 .4 1 1 0 1.3.2 2.5.6 3.6.1.3 0 .7-.2 1z" fill="#fff"/></svg></div>
  <div><div class="lbl">Phone</div><div class="val">+1 555 014 2287</div></div>
</div>

<div class="abs" style="left:142px;top:4723px;width:915px;height:1px;background:rgba(255,255,255,.2)"></div>
<div class="abs" style="left:142px;top:4762px;color:#fff;font-size:13.5px">© 2025 Corvane Athletics. All Rights Reserved &nbsp;|&nbsp; Privacy Policy &nbsp;|&nbsp; Locations &nbsp;|&nbsp; Affiliates &nbsp;|&nbsp; Members</div>
<div class="social" style="left:852px;top:4749px"><i></i></div>
<div class="social on" style="left:907px;top:4749px"><i></i></div>
<div class="social" style="left:959px;top:4749px"><i></i></div>
<div class="social" style="left:1012px;top:4749px"><i></i></div>

</div>
</body>
</html>
```